Yacht, Boats, Watersports company needs a redesign of business card

Hello Designers!
We are a Boat dealership company that sells fun in the water, we sell boats, Yachts, Kayaks and also yacht WaterSport toys. We are looking to redesign our business cards in to something a little bit more sophisticated. in a way that we can make better use of our company colors. I'm attaching a zipped file containing the company 3 sets of company logo which one is an horizontal another one is a vertical and also a chromed 3d logo. Also is included two set of business cards that we use and also some designs that i think it's interesting. We use PMS 2026c Orange and PMS 7687C Blue. I would like to see at least two different options with the orange as accent and also using blue as an accent color. It's really important for the business cards to have a font option and size that is legible to most people. Our current website is wwww.coralpennant.com. Please visit if you want to have a better feeling of the Boat dealership
You can send Single sided or double side options. We are now using single sided but we may be open for a double side option if we really like the design.
Target Market(s)
Marine, boat sales, yacht sales, water toys sales/
Contact Information for Business Card
Name: Dale Whitcombe
Address: 212 North Fenwick Lane,
Palmetto Cove, FL 34417
Phone: 555-731-8842
Fax: 555:731-8843
Cell: 555-382-1490
Email: dw@coralpennant.com
Website: coralpennant.com
Requirements
Must have
- the current information of the business card provided.
logo
use the PMS Colors
Nice to have
- a touch of elegance and sophistication but simple
Should not have
- should not have any typography that is hard to read, the card should be simple but yet sophisticated.

```html
<!DOCTYPE html>
<html lang="en">
<head>
<meta charset="utf-8">
<title>Coral Pennant – Business Card</title>
<link href="https://fonts.googleapis.com/css2?family=Work+Sans:wght@400;500;600;700&display=swap" rel="stylesheet">
<style>
  :root{
    --orange:#e4531f;
    --blue:#1d4477;
    --ink:#4e5358;
    --card:#f4f5f6;
    --backdrop:#dcdad6;
    --edge:#ffffff;
  }
  *{margin:0;padding:0;box-sizing:border-box}
  html,body{width:1200px;height:887px;overflow:hidden}
  body{background:var(--backdrop);font-family:"Work Sans",Arial,sans-serif;position:relative}
  .card{
    position:absolute;left:80px;top:153px;width:1040px;height:580px;
    background:var(--card);border:2px solid var(--edge);border-radius:26px;
    box-shadow:0 10px 30px rgba(0,0,0,.10);
  }
  .brand{position:absolute;left:58px;top:50px;display:flex;align-items:center;gap:16px}
  .brand-dot{width:70px;height:70px;border-radius:50%;border:5px solid var(--orange)}
  .brand-name{font-size:19px;font-weight:600;letter-spacing:.06em;color:var(--blue);text-transform:uppercase}
  .person{position:absolute;left:58px;top:205px;font-size:36px;font-weight:700;letter-spacing:.06em;color:var(--blue);text-transform:uppercase;white-space:nowrap}
  .rule{position:absolute;left:60px;top:272px;width:22px;height:3px;background:var(--orange)}
  .address{position:absolute;left:58px;top:290px;font-size:23px;line-height:32px;letter-spacing:.05em;color:var(--ink)}
  .contacts{position:absolute;left:58px;top:368px;list-style:none;font-size:23px;line-height:32px;letter-spacing:.04em;color:var(--ink)}
  .contacts li{display:flex;align-items:center;gap:8px;white-space:nowrap}
  .contacts svg{width:18px;height:18px;flex:none}
  .contacts .domain{color:var(--blue);font-weight:600}
  .mark{position:absolute;left:502px;top:46px;width:480px;height:480px;border-radius:50%;border:24px solid var(--blue);display:flex;align-items:center;justify-content:center;text-align:center}
  .mark-name{font-size:50px;line-height:60px;font-weight:600;letter-spacing:.06em;color:var(--blue);text-transform:uppercase}
</style>
</head>
<body>
  <div class="card">
    <div class="brand">
      <span class="brand-dot"></span>
      <span class="brand-name">Coral Pennant</span>
    </div>

    <h1 class="person">Dale Whitcombe</h1>
    <span class="rule"></span>

    <p class="address">212 North Fenwick Lane,<br>Palmetto Cove, FL 34417</p>

    <ul class="contacts">
      <li><svg viewBox="0 0 24 24" fill="var(--orange)"><path d="M6.6 10.8a15 15 0 0 0 6.6 6.6l2.2-2.2c.3-.3.7-.4 1-.2 1.1.4 2.3.6 3.6.6.6 0 1 .4 1 1V20c0 .6-.4 1-1 1A17 17 0 0 1 3 4c0-.6.4-1 1-1h3.5c.6 0 1 .4 1 1 0 1.3.2 2.5.6 3.6.1.3 0 .7-.2 1z"/></svg><span>555-731-8842</span></li>
      <li><svg viewBox="0 0 24 24" fill="var(--orange)"><rect x="6" y="3" width="12" height="5"/><rect x="2" y="9" width="20" height="8" rx="2"/><rect x="6" y="14" width="12" height="7"/></svg><span>555:731-8843</span></li>
      <li><svg viewBox="0 0 24 24" fill="none" stroke="var(--orange)" stroke-width="2.4"><rect x="6" y="2" width="12" height="20" rx="2"/><line x1="10" y1="18" x2="14" y2="18"/></svg><span>555-382-1490</span></li>
      <li><svg viewBox="0 0 24 24" fill="none" stroke="var(--orange)" stroke-width="2.2"><rect x="2" y="5" width="20" height="14" rx="1"/><path d="M2 6l10 7 10-7"/></svg><span>dw@coralpennant.com</span></li>
      <li><svg viewBox="0 0 24 24" fill="none" stroke="var(--orange)" stroke-width="2"><circle cx="12" cy="12" r="9.5"/><ellipse cx="12" cy="12" rx="4" ry="9.5"/><line x1="2.5" y1="12" x2="21.5" y2="12"/></svg><span>www.<span class="domain">coralpennant</span>.com</span></li>
    </ul>

    <div class="mark">
      <span class="mark-name">Coral<br>Pennant</span>
    </div>
  </div>
</body>
</html>
```